Business Card Design for Marketing Firm

Looking for business card design for higher end marketing firm. Clean but impressionable/trendy. We are a marketing firm that represents manufacturers in the foodservice equipment and supply industry. Our customers are end users such has hotels, restaurants, country clubs, convention centers and casinos as well as distributors of restaurants supplies and equipment, and manufacturers of foodservice equipment and supplies.
Target Market(s)
Hotels, Restaurants, Supply & Equipment Distributors, Foodservice Manufacturers
Industry/Entity Type
Foodservice/Hospitality
Contact Information for Business Card
Name, Title, Contact Number, Email, Website, Social Media, Address
Requirements
Must have
- Clean & Simple but Serious and Impressionable

```html
<!DOCTYPE html>
<html lang="en">
<head>
<meta charset="utf-8">
<title>Meridian Hospitality Reps – Business Card</title>
<link href="https://fonts.googleapis.com/css2?family=Open+Sans:wght@400;600;700&display=swap" rel="stylesheet">
<style>
  :root {
    --navy: #34346c;
    --paper: #ffffff;
    --ink: #3a3a4a;
    --muted: #6b6b78;
    --backdrop: #e9e6e1;
    --rule: #34346c;
  }
  * { box-sizing: border-box; margin: 0; padding: 0; }
  html, body {
    width: 900px; height: 1200px; overflow: hidden;
    background: var(--backdrop);
    font-family: "Open Sans", Arial, sans-serif;
  }
  .canvas { position: relative; width: 900px; height: 1200px; }
  .card {
    position: absolute; left: 100px; width: 700px; height: 400px;
    border-radius: 26px;
    box-shadow: 0 10px 26px rgba(0,0,0,0.22);
  }
  .card--front { top: 110px; background: var(--paper); }
  .card--back { top: 640px; background: var(--navy); }

  .company-name {
    position: absolute; left: 0; right: 0;
    font-family: "Open Sans", Arial, sans-serif;
    font-weight: 600; text-align: center; line-height: 1.2;
    white-space: nowrap;
  }
  .card--front .company-name { top: 90px; color: var(--navy); font-size: 26px; }
  .card--back .company-name { top: 176px; color: var(--paper); font-size: 38px; }

  .person { position: absolute; left: 56px; top: 210px; }
  .person-name { color: var(--navy); font-weight: 700; font-size: 27px; }
  .person-title { color: var(--muted); font-size: 15px; margin-top: 2px; }

  .divider {
    position: absolute; left: 56px; right: 56px; top: 284px;
    height: 2px; background: var(--rule);
  }
  .contact-list { position: absolute; left: 56px; top: 300px; list-style: none; }
  .contact-list li {
    display: flex; align-items: center; gap: 10px;
    font-size: 14px; color: var(--ink); line-height: 25px;
  }
  .contact-list svg { width: 14px; height: 14px; fill: var(--navy); flex: none; }
  .address {
    position: absolute; left: 410px; top: 327px;
    font-size: 14px; color: var(--ink); line-height: 22px; font-style: normal;
  }
</style>
</head>
<body>
<div class="canvas">
  <section class="card card--front" aria-label="Card front">
    <p class="company-name">Meridian Hospitality Reps</p>
    <div class="person">
      <p class="person-name">Daniel Reyes</p>
      <p class="person-title">CEO &amp; Founder</p>
    </div>
    <div class="divider"></div>
    <ul class="contact-list">
      <li><svg viewBox="0 0 24 24"><path d="M6.6 10.8a15.1 15.1 0 0 0 6.6 6.6l2.2-2.2c.3-.3.7-.4 1-.2 1.1.4 2.3.6 3.6.6.6 0 1 .4 1 1V20c0 .6-.4 1-1 1A17 17 0 0 1 3 4c0-.6.4-1 1-1h3.5c.6 0 1 .4 1 1 0 1.3.2 2.5.6 3.6.1.3 0 .7-.2 1z"/></svg>(555) 014-2290</li>
      <li><svg viewBox="0 0 24 24"><path d="M2 5h20v14H2zm2 2v.5l8 5 8-5V7zm0 2.8V17h16V9.8l-8 5z"/></svg>info@meridianhospreps.com</li>
      <li><svg viewBox="0 0 24 24"><path d="M12 2a10 10 0 1 0 0 20 10 10 0 0 0 0-20zm6.9 9h-3a15 15 0 0 0-1.3-5.6A8 8 0 0 1 18.9 11zM12 4.1c.9 1.3 1.8 3.7 1.9 6.9h-3.8c.1-3.2 1-5.6 1.9-6.9zM9.4 5.4A15 15 0 0 0 8.1 11h-3a8 8 0 0 1 4.3-5.6zM5.1 13h3a15 15 0 0 0 1.3 5.6A8 8 0 0 1 5.1 13zm6.9 6.9c-.9-1.3-1.8-3.7-1.9-6.9h3.8c-.1 3.2-1 5.6-1.9 6.9zm2.6-1.3a15 15 0 0 0 1.3-5.6h3a8 8 0 0 1-4.3 5.6z"/></svg>www.meridianhospreps.com</li>
    </ul>
    <address class="address">450 Harbor Avenue, Suite 210<br>Bayview, CA 90000</address>
  </section>

  <section class="card card--back" aria-label="Card back">
    <p class="company-name">Meridian Hospitality Reps</p>
  </section>
</div>
</body>
</html>
```